Payment company requires web design

We need a web design for a new company based in Singapore.

The company focuses on providing 2 key products: 1) an alternative payment option (i.e. like quib or trelloquin options) on the traditional checkout process 2) a replacement/outsource of a merchants payment page. Key in the UX flow is a end customer dashboard that manages all payments.

We look to provide a simple, fluid and easy to use payment process. The dashboard is minimalistic that allows easy navigation, review of transactions and all available options through gamification.

The final design should communicate ease of use, flexibility and transparency.

Target Market(s)

The value is for the merchant - retail/travel/insurance companies. However its the merchant's end customers that are the target and who the UX is built for.

Industry/Entity Type

It Company

Logo Text

zelnar

Number of Pages Required

5+ page

Colors
ec1f27

Requirements
Must have
• 7 pages mimicking UX flow
• payment page * 2 - 1) alternative payment type 2) outsource of merchants payment page to our business
• our landing page
• end customer verification page
• end customer registration
• customer dashboard
• UX flow in attached file
Nice to have
• open to ideas
• have asked for the logo to be added
• logo to have the colour red (chinese for prosperity)
• the company is all about flexibility, transparency in personal finance management with the option of instalment payments

```html
<!DOCTYPE html>
<html lang="en">
<head>
<meta charset="utf-8">
<title>Zelnar — Payments made simple</title>
<link href="https://fonts.googleapis.com/css2?family=Nunito+Sans:wght@300;400;600&display=swap" rel="stylesheet">
<style>
:root{
  --red:#ec1f27;
  --ink:#333333;
  --muted:#777777;
  --light:#f2f2f2;
  --panel:#e6e6e6;
  --line:#cfcfcf;
  --white:#ffffff;
}
*{box-sizing:border-box;margin:0;padding:0}
html,body{width:1200px;height:2236px;overflow:hidden;background:var(--white)}
body{position:relative;font-family:"Nunito Sans",Arial,sans-serif;color:var(--ink)}
a{color:inherit;text-decoration:none}

/* header */
.site-header{position:absolute;left:0;top:0;width:1200px;height:97px;background:var(--white);box-shadow:0 1px 3px rgba(0,0,0,.12);z-index:2}
.brand{position:absolute;left:145px;top:18px;font-size:46px;font-weight:400;color:var(--red);letter-spacing:-.5px;line-height:1}
.main-nav{position:absolute;top:33px;left:0;width:100%;font-size:18px;font-weight:400;color:var(--ink)}
.main-nav a{position:absolute;white-space:nowrap}
.search-icon{position:absolute;left:903px;top:33px}
.register-btn{position:absolute;left:958px;top:31px;width:99px;height:32px;border:1.5px solid #555;border-radius:2px;font-size:14px;text-align:center;line-height:29px;color:#444}

/* hero */
.hero{position:absolute;left:0;top:97px;width:1200px;height:518px;overflow:hidden}
.hero-photo{position:absolute;inset:0;background:linear-gradient(100deg,#ededed 0%,#e9e9e9 45%,#d9d6d2 65%,#cfc9c2 85%,#e4e6d8 100%)}
.hero-title{position:absolute;left:146px;top:172px;font-size:41px;font-weight:400;color:#555;letter-spacing:.5px}
.hero-subtitle{position:absolute;left:146px;top:224px;font-size:28px;font-weight:400;color:#444;letter-spacing:.3px}
.btn-primary{position:absolute;left:146px;top:281px;width:163px;height:41px;background:var(--red);color:var(--white);font-size:17px;text-align:center;line-height:41px;border-radius:1px}
.slider-dots{position:absolute;left:146px;top:345px;display:flex;gap:9px}
.slider-dots span{width:14px;height:14px;border-radius:50%;background:#c4c4c4}
.slider-dots span:first-child{background:transparent;border:2px solid #c4c4c4}

/* services */
.services{position:absolute;left:0;top:615px;width:1200px;height:289px;background:var(--red)}
.service{position:absolute;top:-39px;width:330px;margin-left:-165px;text-align:center;color:var(--white)}
.service-badge{width:124px;height:124px;margin:0 auto;border-radius:50%;background:var(--red);display:flex;align-items:center;justify-content:center}
.service-badge .ring{width:102px;height:102px;border-radius:50%;border:2.5px solid var(--white);display:flex;align-items:center;justify-content:center}
.service-title{margin-top:21px;font-size:20px;font-weight:400}
.service-text{margin-top:8px;font-size:12px;line-height:17px;padding:0 35px}
.btn-outline-light{display:inline-block;margin-top:17px;width:103px;height:31px;border:1.5px solid var(--white);font-size:13px;line-height:28px}

/* about */
.about{position:absolute;left:0;top:904px;width:1200px;height:355px;text-align:center}
.section-heading{position:absolute;left:0;top:62px;width:100%;font-size:32px;font-weight:300;color:var(--ink);letter-spacing:.5px}
.heading-rule{position:absolute;top:84px;width:57px;height:1px;background:#999}
.about-text{position:absolute;left:190px;top:125px;width:830px;font-size:15px;line-height:28px;color:var(--muted)}
.btn-outline-dark{position:absolute;left:526px;top:257px;width:143px;height:40px;border:1.5px solid #bdbdbd;font-size:14px;line-height:37px;color:#666;letter-spacing:.3px}

/* faq */
.faq{position:absolute;left:0;top:1259px;width:1200px;height:445px;background:var(--light)}
.faq-heading{position:absolute;left:0;top:31px;width:100%;text-align:center;font-size:30px;font-weight:300;color:#222}
.faq-list{position:absolute;left:219px;top:84px;width:765px}
.faq-q{height:46px;padding-left:20px;font-size:16px;line-height:46px;background:var(--panel);border:1px solid #d6d6d6;border-top:none;color:#444}
.faq-q.is-open{height:43px;line-height:43px;background:var(--red);color:var(--white);border:none}
.faq-a{height:119px;background:var(--white);border:1px solid #d6d6d6;border-top:none;padding:14px 20px;display:flex;gap:12px}
.faq-a .label{color:var(--red);font-size:16px}
.faq-a p{font-size:12px;line-height:22px;color:#8a8a8a;padding-top:2px}

/* customer services */
.support{position:absolute;left:0;top:1704px;width:1200px;height:364px;background:var(--white);border-top:1px solid #e4e4e4;overflow:hidden}
.support-photo{position:absolute;left:640px;top:0;width:560px;height:364px;background:linear-gradient(120deg,#f6f6f6 0%,#eeeeee 30%,#cfcfcf 55%,#3a3a3a 75%,#d9c7a2 90%,#1c1c1c 100%)}
.support-title{position:absolute;left:162px;top:91px;font-size:32px;font-weight:400;color:var(--red);letter-spacing:.3px}
.support-text{position:absolute;left:164px;top:143px;width:490px;font-size:14px;line-height:23px;color:#666}
.search-form{position:absolute;left:161px;top:228px;width:359px;height:38px;border:1px solid #cfcfcf;border-radius:19px;background:var(--white)}
.search-form .placeholder{position:absolute;left:19px;top:0;line-height:36px;font-size:13px;color:#aaa}
.search-form .search-btn{position:absolute;right:-1px;top:-1px;width:105px;height:38px;border-radius:19px;background:var(--red);color:var(--white);font-size:17px;text-align:center;line-height:38px}

/* footer */
.site-footer{position:absolute;left:0;top:2068px;width:1200px;height:168px;background:var(--white);border-top:1px solid #e4e4e4}
.footer-nav{position:absolute;top:42px;left:0;width:100%;font-size:17px;color:#444}
.footer-nav a{position:absolute;transform:translateX(-50%);white-space:nowrap}
.copyright{position:absolute;top:71px;left:0;width:100%;text-align:center;font-size:11px;color:#888}
.social{position:absolute;top:107px;left:535px;display:flex;gap:3px}
.social span{width:31px;height:31px;border-radius:50%;border:1.5px solid #555}
</style>
</head>
<body>

<header class="site-header">
  <a class="brand" href="#">Zelnar</a>
  <nav class="main-nav">
    <a href="#" style="left:417px">Home</a>
    <a href="#" style="left:505px">About</a>
    <a href="#" style="left:594px">How it work</a>
    <a href="#" style="left:730px">Services</a>
    <a href="#" style="left:836px">FAQ</a>
  </nav>
  <svg class="search-icon" width="22" height="22" viewBox="0 0 22 22" aria-label="Search"><circle cx="9" cy="9" r="6.5" fill="none" stroke="#8a8a8a" stroke-width="2.6"/><line x1="14" y1="14" x2="20" y2="20" stroke="#8a8a8a" stroke-width="3" stroke-linecap="round"/></svg>
  <a class="register-btn" href="#">Register</a>
</header>

<section class="hero">
  <div class="hero-photo" role="img" aria-label="Photo of hands holding a smartphone showing a checkout screen on a white desk with a keyboard, earphones and a green cup"></div>
  <h1 class="hero-title">Maecenas aliquet velit</h1>
  <p class="hero-subtitle">Neque metus malesuada nec</p>
  <a class="btn-primary" href="#">Get Started</a>
  <div class="slider-dots"><span></span><span></span><span></span><span></span></div>
</section>

<section class="services">
  <div class="service" style="left:276px">
    <div class="service-badge"><div class="ring">
      <svg width="58" height="54" viewBox="0 0 58 54" aria-hidden="true"><path d="M6 4h46l4 16H2z" fill="#fff"/><path d="M2 20h54v4c0 4-4 6-7 6s-6-2-6-6c0 4-3 6-7 6s-7-2-7-6c0 4-3 6-7 6s-7-2-7-6c0 4-3 6-6 6s-7-2-7-6z" fill="#fff"/><rect x="8" y="32" width="42" height="20" fill="#fff"/><rect x="22" y="36" width="14" height="16" fill="#ec1f27"/><path d="M15 4l-3 16M25 4l-1 16M33 4l1 16M43 4l3 16" stroke="#ec1f27" stroke-width="2"/></svg>
    </div></div>
    <h2 class="service-title">Merchant Payment</h2>
    <p class="service-text">sociosqu ad litora torquent per conubia nostra per inceptos hymenaeos Proin nulla arcu nonummy luctus</p>
    <a class="btn-outline-light" href="#">Read More</a>
  </div>
  <div class="service" style="left:604px">
    <div class="service-badge"><div class="ring">
      <svg width="58" height="58" viewBox="0 0 58 58" aria-hidden="true"><rect x="10" y="4" width="22" height="12" fill="#fff"/><rect x="4" y="16" width="34" height="20" rx="3" fill="#fff"/><rect x="10" y="30" width="22" height="14" fill="#fff" stroke="#ec1f27" stroke-width="2"/><g transform="rotate(-30 40 40)"><rect x="26" y="30" width="30" height="20" rx="2" fill="#fff" stroke="#ec1f27" stroke-width="2"/><rect x="26" y="35" width="30" height="4" fill="#ec1f27"/></g></svg>
    </div></div>
    <h2 class="service-title">Outsourced Payment</h2>
    <p class="service-text">sociosqu ad litora torquent per conubia nostra per inceptos hymenaeos Proin nulla arcu nonummy luctus</p>
    <a class="btn-outline-light" href="#">Read More</a>
  </div>
  <div class="service" style="left:933px">
    <div class="service-badge"><div class="ring">
      <svg width="58" height="54" viewBox="0 0 58 54" aria-hidden="true"><rect x="12" y="2" width="22" height="16" rx="2" fill="#fff" transform="rotate(-15 23 10)"/><rect x="22" y="4" width="22" height="16" rx="2" fill="#fff" stroke="#ec1f27" stroke-width="1.5" transform="rotate(10 33 12)"/><rect x="4" y="16" width="48" height="34" rx="4" fill="#fff"/><rect x="38" y="26" width="16" height="12" rx="3" fill="#fff" stroke="#ec1f27" stroke-width="2"/><circle cx="44" cy="32" r="2" fill="#ec1f27"/></svg>
    </div></div>
    <h2 class="service-title">Installment Payments</h2>
    <p class="service-text">sociosqu ad litora torquent per conubia nostra per inceptos hymenaeos Proin nulla arcu nonummy luctus</p>
    <a class="btn-outline-light" href="#">Read More</a>
  </div>
</section>

<section class="about">
  <span class="heading-rule" style="left:413px"></span>
  <h2 class="section-heading">About Zelnar</h2>
  <span class="heading-rule" style="left:715px"></span>
  <p class="about-text">Etiam eleifend metus vitae adipiscing semper mauris ipsum iaculis elit congue gravida elit mi Maecenas aliquet velit vel turpis Mauris neque metus malesuada nec ultricies sit amet porttitor mattis enim In massa libero interdum nec interdum vel blandit sed nulla In ullamcorper est eget tempor cursus neque mi consectetuer mi a ultricies massa est sed nisl Class aptent taciti sociosqu ad litora torquent per conubia nostra per inceptos</p>
  <a class="btn-outline-dark" href="#">READ MORE</a>
</section>

<section class="faq">
  <h2 class="faq-heading">FAQ</h2>
  <div class="faq-list">
    <div class="faq-q is-open">Q: Etiam est nunc venenatis in tristique eu imperdiet ac nisl Cum sociis natoque?</div>
    <div class="faq-a">
      <span class="label">A:</span>
      <p>Maecenas at justo id velit placerat molestie Donec dictum lectus non odio Cras a ante vitae enim iaculis aliquam Mauris nunc quam venenatis nec euismod sit amet egestas placerat est Pellentesque habitant morbi tristique senectus et netus et malesuada fames ac turpis egestas Cras id elit Integer quis urna Ut ante enim</p>
    </div>
    <div class="faq-q">Q: Morbi porta libero ullamcorper nonummy nibh ligula ?</div>
    <div class="faq-q">Q:&nbsp; Pulvinar metus eget consectetuer augue nisi quis lacus Ut ac mi?</div>
    <div class="faq-q">Q: Auis lacus mollis aliquam Curabitur iaculis tempus?</div>
  </div>
</section>

<section class="support">
  <div class="support-photo" role="img" aria-label="Photo of a white desk with a laptop keyboard, a notebook, a smartphone and a cup of coffee"></div>
  <h2 class="support-title">Customer Services</h2>
  <p class="support-text">Curabitur vel mi sit amet magna malesuada ultrices Ut nisi erat fermentum vel congue id euismod in elit Fusce ultricies orci ac feugiat suscipit leo massa sodales velit et scelerisque mi tortor at</p>
  <div class="search-form">
    <span class="placeholder">Type here</span>
    <span class="search-btn">Search</span>
  </div>
</section>

<footer class="site-footer">
  <nav class="footer-nav">
    <a href="#" style="left:364px">Home</a>
    <a href="#" style="left:447px">About</a>
    <a href="#" style="left:552px">How it work</a>
    <a href="#" style="left:665px">Services</a>
    <a href="#" style="left:748px">FAQ</a>
    <a href="#" style="left:832px">Contact</a>
  </nav>
  <p class="copyright">© 2016 Company Name&nbsp; All right reserved&nbsp; Term of Use</p>
  <div class="social"><span></span><span></span><span></span><span></span></div>
</footer>

</body>
</html>
```